Wine Label for a Sweet Wine Called "Glimmo"

We need a wine label that will be used for both a sweet red and a sweet white wine. The very important thing to remember is the target market for these wines is: young American women who love sweet wines and they also spend a lot of their money on their hair, clothes, jewelry, nails. They LOVE Glimmo (Glimmo is a word used to describe flashy accessories, jewelry, decoration.) This label needs to be eye catching, showy, fun, glittery. Please put the brand name, "Glimmo," big, and then in smaller but still readable words underneath the label or somewhere on the label: Sweet, Sophisticated, Red (or white). (An example of what I mean is attached). To differentiate between the two color wines you can suggest color changes to differentiate between the red label and the white label but the label design itself should be the same. Ultimately, the label can be the exact same label for both white and red as long as it looks good on a white wine (a greenish/yellow wine in a clear glass bottle) and a red wine (a dark color wine in a dark bottle).

I've attached an example of the text size relationship between the word Glimmo and the words to go underneath or elsewhere on the label, but you can certainly play with this-- it is just a suggestion of the text size relationship, and definitely NOT at all mandatory that you use any of these fonts.

You can pick the size of the label but try to stay within normal wine label sizes, meaning don't go bigger than approx. 3.5 inches wide and 5 inches tall.

Target Market(s)

Young American women who love sweet wines and spend a lot of money on their hair, clothes, jewelry, nails. They love Glimmo (Glimmo is a word that means flashy accessories, jewelry, decoration)

Requirements
Must have
• It needs to be flashy, glittery, fun, eye catching, memorable
Nice to have
• It shouldn't be too too ultra feminine! The target market is strong independent women and we also have men who will buy it too.

```html
<!DOCTYPE html>
<html lang="en">
<head>
<meta charset="utf-8">
<title>Glimmo wine labels</title>
<link href="https://fonts.googleapis.com/css2?family=Playfair+Display:wght@900&family=Josefin+Sans:wght@400&display=swap" rel="stylesheet">
<style>
  :root{
    --stage-light:#dcd6a8;
    --stage-mid:#7d7864;
    --stage-dark:#0c0306;
    --gold-deep:#7a4e12;
    --gold:#c99a3a;
    --gold-bright:#f3d88a;
    --white-glow:#fffbee;
    --white-cream:#ecd9a0;
    --white-amber:#c59a3c;
    --red-deep:#8a0d0d;
    --red:#c8221b;
    --red-glow:#f26a5a;
    --ink-dark:#1a1a17;
    --ink-light:#ffffff;
  }
  *{margin:0;padding:0;box-sizing:border-box}
  html,body{width:1200px;height:929px;overflow:hidden}
  body{
    position:relative;
    background:linear-gradient(90deg,var(--stage-light) 0%,var(--stage-light) 39%,var(--stage-mid) 52%,var(--stage-dark) 64%,var(--stage-dark) 100%);
  }
  .label{
    position:absolute;
    width:461px;height:657px;
    overflow:hidden;
    box-shadow:6px 8px 10px rgba(0,0,0,.45);
  }
  .label--white{
    left:94px;top:70px;
    background:radial-gradient(ellipse 60% 45% at 52% 45%,var(--white-glow) 0%,var(--white-cream) 55%,var(--white-amber) 100%);
  }
  .label--red{
    left:646px;top:132px;
    background:
      radial-gradient(ellipse 45% 35% at 58% 70%,rgba(255,200,190,.75) 0%,rgba(242,106,90,.4) 45%,rgba(242,106,90,0) 100%),
      radial-gradient(ellipse 70% 60% at 50% 55%,var(--red) 0%,var(--red-deep) 100%);
  }
  .glitter{position:absolute;left:0;width:100%;display:block}
  .glitter--top{top:0;height:70px}
  .glitter--bottom{bottom:0;height:80px}
  .brand{
    position:absolute;left:0;width:100%;
    text-align:center;
    font-family:"Playfair Display",serif;
    font-weight:900;
    font-size:112px;
    line-height:1;
    letter-spacing:-2px;
  }
  .label--white .brand{top:190px;color:var(--ink-dark)}
  .label--red .brand{top:104px;color:var(--ink-light)}
  .tagline{
    position:absolute;left:0;width:100%;
    text-align:center;
    font-family:"Josefin Sans",sans-serif;
    font-size:16px;
    letter-spacing:4.2px;
    white-space:nowrap;
  }
  .tagline .sep{display:inline-block;width:1px;height:16px;margin:0 6px -2px;background:currentColor}
  .label--white .tagline{top:326px;color:var(--ink-dark)}
  .label--red .tagline{top:254px;color:var(--ink-light)}
</style>
</head>
<body>
  <svg width="0" height="0" style="position:absolute">
    <defs>
      <linearGradient id="goldBand" x1="0" y1="0" x2="1" y2="1">
        <stop offset="0" stop-color="#8a5a18"/>
        <stop offset=".3" stop-color="#e2bb5e"/>
        <stop offset=".55" stop-color="#a8761f"/>
        <stop offset=".8" stop-color="#f0cf78"/>
        <stop offset="1" stop-color="#7a4e12"/>
      </linearGradient>
    </defs>
  </svg>

  <section class="label label--white">
    <svg class="glitter glitter--top" viewBox="0 0 461 70" preserveAspectRatio="none" role="img" aria-label="Gold glitter wave band">
      <path d="M0 0H461V40C380 58 300 30 220 52C140 72 70 44 0 60Z" fill="url(#goldBand)"/>
    </svg>
    <h1 class="brand">Glimmo</h1>
    <p class="tagline">SWEET<span class="sep"></span>WHITE<span class="sep"></span>SOPHISTICATED</p>
    <svg class="glitter glitter--bottom" viewBox="0 0 461 80" preserveAspectRatio="none" role="img" aria-label="Gold glitter wave band">
      <path d="M0 14C90 0 170 22 250 10C330 0 400 18 461 6V80H0Z" fill="url(#goldBand)"/>
    </svg>
  </section>

  <section class="label label--red">
    <svg class="glitter glitter--top" viewBox="0 0 461 70" preserveAspectRatio="none" role="img" aria-label="Gold glitter wave band">
      <path d="M0 0H461V42C380 60 300 32 220 54C140 72 70 46 0 62Z" fill="url(#goldBand)"/>
    </svg>
    <h1 class="brand">Glimmo</h1>
    <p class="tagline">SWEET<span class="sep"></span>RED<span class="sep"></span>SOPHISTICATED</p>
    <svg class="glitter glitter--bottom" viewBox="0 0 461 80" preserveAspectRatio="none" role="img" aria-label="Gold glitter wave band">
      <path d="M0 12C90 0 170 20 250 8C330 0 400 16 461 4V80H0Z" fill="url(#goldBand)"/>
    </svg>
  </section>
</body>
</html>
```